New B2C website design to help dads be better dads

DadHarbor is a website to help dads be the “best dad you can be.”

We require our website to be designed into a PSD format, no coding necessary.

The general concept is a two-page design. The first page is the login page, the second page is the home page. Once at the home page, rather than navigating to and from different pages, the user will push and pull through different visual and functional layers of the hierarchy. In theory, this should add to the user experience by having a visual anchor of where they are (through layered pagination) as well as improving loading times since the new information should only be a delta in data load versus a brand new page load.

The general look-and-feel we are going for is clean, simple, minimal. This means that the winning design will show us a good eye for web-optimized typography, good use of white (negative) space, and good use of a visually pleasing grid.

We require a total of 6 page "views" plus the landing page. We note that many of the views are similar to one another.
Landing page
Milestone view
Task view
Content view, articles
Content view, products
Search view
What's new view

Please review all of the additional information provided as well as the attachments for examples.

We provide the following websites as good references for:

Typography:
http://example-kelvorn.com/journal/

Use of white space:
http://www.trenvaskit.com/
http://moldrefin.com/

Example for “scrolling” page concept as well as good balance of color, typography, and white space:
http://www.qorbitalmeet.eu/

Please contact us with questions so that we can guide your design effort.
Updates

Hello designers,

The following information is added to help guide the design process:

1.  For the text dialogue below the landing page, please assume the following word count:
"why are we making dad harbor?": 250 words
"who are we?" 200 words
"what's the deal with the penguin logo?" 300 words

For the social media links, please see http://www.gravelplumbs.com/
Notice the floating "social" bar that is always to the right.  This is the concept we are going for, please try to implement this as you see fit. 

Target Market(s)

Fathers of young children ages 0-6 years old.

Industry/Entity Type

Product

Font styles to use
Sans Serif

Requirements
Must have
• Clean lines, minimal design concept

Incorporation of our logo (see attached document)

Header content is static for all views after landing page, see example

This page WILL be responsive, please keep that in mind when designing
The timeline bar should be to the left, with the timeline bar’s “milestones” also being responsive.

Designer is free to suggest font types, but any fonts used must be royalty-free and web-optimized. We request a minimum number of font types as well as fonts that load relatively fast. We reinforce that visually appealing typography is a significant factor in the winning design choice.

While we are not expecting the winning design to include code, please keep in mind that the final implementation needs to be optimized for desktop, tablet, and mobile platforms.

If you are using stock photography that is not generated by you, please provide where/how we can obtain imagery, as well as price.

All custom graphics must be available in original formats; Photoshop/GIMP layered files for layout design, and vector formats for logos, icons and other graphical elements.

Please incorporate “Blue” into design elements as you see fit, as the RGB 67 74 169 Blue is the primary color used in our brand. The complement to this blue is 255 202 0, a brownish orange. Feel free to use this color as well, although please keep it to a lesser amount.

Background color is your choice, do not feel the need to use the grey.
Should not have
• Excessive graphical content such that it affects loading times

Excessive use of too many font types such that it affects loading times

```html
<!DOCTYPE html>
<html lang="en">
<head>
<meta charset="utf-8">
<title>DadHarbor – Prepare for the baby arrival</title>
<link href="https://fonts.googleapis.com/css2?family=Francois+One&family=Noto+Sans:wght@400;700&family=Poiret+One&family=Raleway:wght@400&display=swap" rel="stylesheet">
<style>
:root{
  --brand-blue:#1d2d6b;
  --link-blue:#3f4ca9;
  --accent-orange:#f0a80c;
  --text:#333333;
  --muted:#555555;
  --border:#d6d6d6;
  --check-off:#e4e4e4;
  --star-on:#f5b91d;
  --star-off:#d4d4d4;
  --page:#ffffff;
}
*{box-sizing:border-box;margin:0;padding:0}
html,body{width:1200px;height:1153px;overflow:hidden;background:var(--page)}
body{position:relative;font-family:"Noto Sans",Arial,sans-serif;color:var(--text)}

.site-header{position:absolute;left:0;top:0;width:1200px;height:138px;
  background:linear-gradient(#ffffff,#e3e3e3);border-bottom:4px solid var(--brand-blue)}
.brand{position:absolute;left:34px;top:22px;width:110px;text-align:center}
.brand-mark{display:block;width:54px;height:54px;border-radius:50%;background:var(--brand-blue);margin:0 auto 8px}
.brand-name{font-weight:700;font-size:15px;color:var(--brand-blue)}
.welcome{position:absolute;left:193px;top:14px;font-family:"Francois One",sans-serif;font-size:39px;font-weight:400;color:#111;letter-spacing:.3px}
.dad-score{position:absolute;left:193px;top:86px;font-size:16px;color:#222}
.dad-score strong{color:var(--brand-blue)}
.search-field{position:absolute;left:438px;top:77px;width:300px;height:43px;border:1px solid #ccc;border-radius:4px;background:#fff}
.btn{position:absolute;top:77px;height:43px;background:var(--brand-blue);color:#fff;border-radius:4px;
  font-weight:700;font-size:16px;letter-spacing:.5px;display:flex;align-items:center;justify-content:center}
.btn-search{left:748px;width:114px}
.btn-logout{left:1058px;width:114px}
.account-link{position:absolute;left:959px;top:86px;font-size:16px;color:#222}

.section-band{position:absolute;left:0;top:142px;width:1200px;height:48px;background:var(--accent-orange)}
.section-band h1{position:absolute;left:56px;top:8px;font-weight:400;font-size:25px;color:#1a1a1a}
.band-pointer{position:absolute;left:72px;top:189px}

.task-list{position:absolute;left:56px;top:232px;width:263px;height:289px;border:2px solid #e2e2e2;border-radius:6px;list-style:none;padding:22px 0 0 20px}
.task-list li{display:flex;align-items:center;height:33px;font-size:17px;color:#333}
.check{width:20px;height:20px;border-radius:3px;background:var(--check-off);margin-right:14px;flex:none;position:relative}
.check.done{background:#6fa8e8;border:1px solid #3a74c4}

.card{position:absolute;width:251px;height:319px;border:1px solid var(--border);background:#fff;padding:4px}
.card-media{height:145px;background:linear-gradient(135deg,#5a4a3e,#b98f72 55%,#e2d3c4)}
.card-media.product{background:linear-gradient(135deg,#ffffff,#8c9277 50%,#ffffff)}
.card-body{padding:0 5px}
.card-type{margin-top:11px;font-weight:700;font-size:17px;color:var(--brand-blue)}
.card-meta{display:flex;justify-content:space-between;align-items:center;margin-top:12px;font-size:15px}
.card-meta b{font-weight:400;color:var(--brand-blue)}
.stars{display:flex;gap:2px}
.card-text{margin-top:12px;font-size:14.6px;line-height:19px;color:#333}

.sort{position:absolute;left:953px;top:222px;font-size:16px;color:#222}
.sort-select{position:absolute;left:953px;top:246px;width:116px;height:27px;border:1px solid #ccc;font-size:14px;color:#555;padding:4px 7px}
.sort-select svg{position:absolute;right:8px;top:10px}

.contact{position:absolute;left:0;top:955px;width:1200px;text-align:center}
.contact-label{font-weight:700;font-size:15px;letter-spacing:4px;color:#555}
.contact-title{margin-top:18px;font-family:"Poiret One",sans-serif;font-size:46px;color:#111;font-weight:400}
.contact-email{margin-top:14px;font-weight:700;font-size:20px;color:var(--link-blue)}
.legal{margin-top:26px;font-family:"Raleway",sans-serif;font-size:13.5px;color:#555}
.legal span{margin:0 6px}
</style>
</head>
<body>
<svg width="0" height="0" style="position:absolute">
  <defs>
    <polygon id="star" points="9,1 11.4,6.5 17.3,6.9 12.8,10.8 14.2,16.6 9,13.5 3.8,16.6 5.2,10.8 0.7,6.9 6.6,6.5"/>
  </defs>
</svg>

<header class="site-header">
  <div class="brand"><span class="brand-mark"></span><span class="brand-name">DadHarbor</span></div>
  <div class="welcome">Welcome Greg, what would you like to do today?</div>
  <div class="dad-score">Super Dad Score: <strong>10,500</strong></div>
  <div class="search-field"></div>
  <div class="btn btn-search">SEARCH</div>
  <div class="account-link">My account</div>
  <div class="btn btn-logout">LOGOUT</div>
</header>

<div class="section-band"><h1>Prepare for the baby arrival</h1></div>
<svg class="band-pointer" width="42" height="23" viewBox="0 0 42 23"><polygon points="0,0 42,0 21,23" fill="var(--accent-orange)"/></svg>

<ul class="task-list">
  <li><span class="check"></span>Buy a crib</li>
  <li><span class="check"></span>As semble the crib</li>
  <li><span class="check"></span>Buy a stroller</li>
  <li><span class="check done"><svg width="18" height="18" viewBox="0 0 18 18"><path d="M4 9.5l3.2 3.2L14 5" stroke="#123a7a" stroke-width="2.4" fill="none"/></svg></span>Buy a carseat</li>
  <li><span class="check"></span>Install a carseat</li>
  <li><span class="check"></span>Learn to change a diaper</li>
  <li><span class="check"></span>Learn to hold a baby</li>
  <li><span class="check"></span>Set a feeding schedule</li>
</ul>

<article class="card" style="left:349px;top:232px">
  <div class="card-media" role="img" aria-label="Photo of a father buckling his baby into a car seat"></div>
  <div class="card-body">
    <div class="card-type">ARTICLE</div>
    <div class="card-meta"><span class="stars"><svg width="18" height="18"><use href="#star" fill="var(--star-on)"/></svg><svg width="18" height="18"><use href="#star" fill="var(--star-on)"/></svg><svg width="18" height="18"><use href="#star" fill="var(--star-on)"/></svg><svg width="18" height="18"><use href="#star" fill="var(--star-off)"/></svg><svg width="18" height="18"><use href="#star" fill="var(--star-off)"/></svg></span><span><b>3,121</b> ratings</span></div>
    <p class="card-text">I went out to buy my first car seat and had to earn my PhD in car seats, Newtonian physics, and anti-stain technology...</p>
  </div>
</article>

<article class="card" style="left:637px;top:232px">
  <div class="card-media product" role="img" aria-label="Product photo of a green stroller with matching infant carrier"></div>
  <div class="card-body">
    <div class="card-type">PRODUCT</div>
    <div class="card-meta"><span class="stars"><svg width="18" height="18"><use href="#star" fill="var(--star-on)"/></svg><svg width="18" height="18"><use href="#star" fill="var(--star-on)"/></svg><svg width="18" height="18"><use href="#star" fill="var(--star-on)"/></svg><svg width="18" height="18"><use href="#star" fill="var(--star-off)"/></svg><svg width="18" height="18"><use href="#star" fill="var(--star-off)"/></svg></span><span><b>9,102</b> likes</span></div>
    <p class="card-text">The Larvik XT stroller is this year’s hottest stroller, for more reasons than are obvious. What we particularly like about it is...</p>
  </div>
</article>

<article class="card" style="left:349px;top:580px">
  <div class="card-media" role="img" aria-label="Photo of a father buckling his baby into a car seat"></div>
  <div class="card-body">
    <div class="card-type">ARTICLE</div>
    <div class="card-meta"><span class="stars"><svg width="18" height="18"><use href="#star" fill="var(--star-on)"/></svg><svg width="18" height="18"><use href="#star" fill="var(--star-on)"/></svg><svg width="18" height="18"><use href="#star" fill="var(--star-on)"/></svg><svg width="18" height="18"><use href="#star" fill="var(--star-off)"/></svg><svg width="18" height="18"><use href="#star" fill="var(--star-off)"/></svg></span><span><b>1,595</b> likes</span></div>
    <p class="card-text">I learned something new this week which made my penny-pinching side just giddy. Car seats double as airplane...</p>
  </div>
</article>

<article class="card" style="left:637px;top:580px">
  <div class="card-media" role="img" aria-label="Photo of a father buckling his baby into a car seat"></div>
  <div class="card-body">
    <div class="card-type">ARTICLE</div>
    <div class="card-meta"><span class="stars"><svg width="18" height="18"><use href="#star" fill="var(--star-on)"/></svg><svg width="18" height="18"><use href="#star" fill="var(--star-on)"/></svg><svg width="18" height="18"><use href="#star" fill="var(--star-on)"/></svg><svg width="18" height="18"><use href="#star" fill="var(--star-off)"/></svg><svg width="18" height="18"><use href="#star" fill="var(--star-off)"/></svg></span><span><b>9,007</b> likes</span></div>
    <p class="card-text">Don’t forget your go-bag essentials! Camping gear aside, Trailkin Supply has assembled a great kit to take...</p>
  </div>
</article>

<div class="sort">Sort by:</div>
<div class="sort-select">Most recent<svg width="11" height="7" viewBox="0 0 11 7"><polygon points="0,0 11,0 5.5,7" fill="var(--brand-blue)"/></svg></div>

<footer class="contact">
  <div class="contact-label">CONTACT</div>
  <div class="contact-title">GET IN TOUCH</div>
  <div class="contact-email">info@dadharbor.com</div>
  <div class="legal">Privacy Policy<span>|</span>© 2013 DadHarbor<span>|</span>Terms Policy<span>|</span>Disclaimer</div>
</footer>
</body>
</html>
```